GearHive.com

Our company, GearHive Inc., is an established business with an extensive worldwide customer base in the Aviation, Aerospace, and Defense Industries.
GearHive Inc, is an e-commerce platform driven by an aviation parts locator. We are looking to totally redo our homepage, log-in page, standard part search page, and results page.
Our current web design is in 800frame and we need it to be updated to a centered 1280 frame. The new design also needs to be easily viewed from any mobile device. The new size needs to accommodate 2-3 advertisements, both vertically and horizontally.
I like clean, simple, crisp lines that can easily be navigated by everyone. Along with Aviation/Aerospace stock photos, I would like to use different shades of blue and grey and accent specific buttons/drop-downs with orange or yellow.
We are also looking for a web designer who also has the ability to cut up the page and turn over to our .NET developers.
Attached are the 4 pages that I would like to start working on. The standard content within these pages need to be incorporated into the new design.
Our current website is www.gearhive.com
Below are some industry websites that I like the color and feel of.
Please use attached pic of corvane T410 as main photo
http://www.stravelcorp.com/
http://www.quillanor.com/en/aerospace.html
http://www.dexavend.com/
http://aerospace.veltrimax.com/

```html
<!DOCTYPE html>
<html lang="en">
<head>
<meta charset="utf-8">
<title>GearHive – Home</title>
<link rel="stylesheet" href="https://fonts.googleapis.com/css2?family=Open+Sans:wght@400;600;700&family=Roboto+Condensed:wght@700&family=Arimo:wght@400;700&display=swap">
<style>
:root{
  --brand-blue:#1a5fb4;
  --link-blue:#1466b8;
  --navy:#1b2a8c;
  --nav-top:#2a7fe0;
  --nav-bottom:#0b3fa8;
  --orange:#f07b1a;
  --text:#222;
  --muted:#777;
  --rule:#d8d8d8;
  --footer:#2f2e2e;
  --footer-base:#262525;
  --date:#1a73c9;
}
*{margin:0;padding:0;box-sizing:border-box}
html,body{width:982px;height:1200px;overflow:hidden;background:#fff}
body{position:relative;font-family:"Open Sans",sans-serif;color:var(--text)}
.abs{position:absolute}

.top-border{left:0;top:0;width:982px;height:3px;background:#222}
.brand{left:116px;top:36px;font-size:38px;font-weight:700;color:var(--brand-blue);letter-spacing:-1px}
.utility{right:116px;top:49px;display:flex;align-items:center;gap:8px;font-size:11px;font-weight:600;color:var(--link-blue)}
.utility span{display:flex;align-items:center;gap:5px}
.utility .sep{color:#333}
.utility svg{width:14px;height:13px}

.main-nav{left:0;top:114px;width:982px;height:41px;background:linear-gradient(var(--nav-top),var(--nav-bottom))}
.main-nav a{position:absolute;top:13px;color:#fff;font-size:11.5px;font-weight:600;text-decoration:none}

.hero{left:0;top:155px;width:982px;height:334px;background:linear-gradient(180deg,#3b7cc0 0%,#6da4d6 40%,#b7d2ea 75%,#e6eef6 100%)}
.hero-caption{left:0;top:167px;width:668px;height:115px;background:rgba(40,50,65,.45)}
.hero-title{left:116px;top:183px;color:#fff;font-size:18.5px;font-weight:600;white-space:nowrap}
.hero-text{left:116px;top:209px;width:520px;color:#fff;font-size:12px;font-weight:600;line-height:16px}
.hero-btn{left:116px;top:250px;width:77px;height:20px;background:var(--orange);color:#fff;font-size:9.5px;font-weight:600;text-align:center;line-height:20px}
.dots{left:446px;top:308px;display:flex;gap:6px}
.dots i{width:10px;height:10px;border-radius:50%;background:#ccc;border:1px solid #aaa}
.dots i.on{background:#fff;border:3px solid var(--brand-blue)}

.card{top:519px;width:169px;height:192px;border:1px solid #e0e0e0;box-shadow:0 1px 3px rgba(0,0,0,.08);background:#fff}
.card-media{position:absolute;left:8px;top:12px;width:153px;height:88px}
.card h3{position:absolute;left:9px;top:110px;font-size:12.5px;font-weight:600;color:var(--navy)}
.card p{position:absolute;left:10px;top:128px;width:152px;font-size:9.5px;line-height:14px;color:var(--muted)}
.card .more{position:absolute;left:11px;top:162px;font-size:10.5px;font-weight:600;color:#222}

.section-title{font-size:15px;font-weight:600;color:var(--navy)}
.rule{height:1px;background:var(--rule)}
.welcome p{position:absolute;left:117px;width:353px;font-family:"Arimo",sans-serif;font-size:9px;line-height:13.7px;text-align:justify;color:#222}

.news-thumb{left:513px;width:48px;height:47px}
.news-text{left:572px;width:294px;font-family:"Arimo",sans-serif;font-size:9px;line-height:13.7px;color:#222}
.news-date{left:574px;font-family:"Arimo",sans-serif;font-size:9px;font-weight:700;color:var(--date)}

.footer{left:0;top:1005px;width:982px;height:160px;background:var(--footer)}
.footer-base{left:0;top:1165px;width:982px;height:35px;background:var(--footer-base);color:#ddd;font-family:"Arimo",sans-serif;font-size:9.5px;text-align:center;line-height:35px}
.f-col{top:1022px;display:flex;flex-direction:column;gap:9.8px;font-family:"Arimo",sans-serif;font-size:9.5px;color:#fff}
.news-head{left:524px;top:1021px;font-family:"Roboto Condensed",sans-serif;font-size:12px;color:#fff}
.field{left:523px;width:161px;height:25px;background:#fff;font-family:"Arimo",sans-serif;font-size:9px;color:#333;padding:6px 6px}
.signup{left:523px;top:1123px;width:76px;height:25px;background:#1760ad;color:#fff;font-family:"Roboto Condensed",sans-serif;font-size:14px;text-align:center;line-height:25px}
.contact{left:762px;top:1022px;width:110px;font-family:"Arimo",sans-serif;font-size:10px;line-height:14.5px;color:#fff}
.social{left:733px;top:1128px;display:flex;gap:6px}
.social i{width:22px;height:22px;border-radius:50%;background:#4d7fc4}
</style>
</head>
<body>

<div class="abs top-border"></div>
<div class="abs brand">GearHive</div>

<nav class="abs utility">
  <span><svg viewBox="0 0 14 13"><path d="M1 7l5-1 4-5h2l-2 5 3 0 1-2h1l-1 3 1 3h-1l-1-2-3 0 2 5h-2L6 8 1 7z" fill="#444"/></svg>AERO PAGES</span><span class="sep">/</span>
  <span><svg viewBox="0 0 14 13"><rect x="1" y="2" width="12" height="9" fill="#444"/><path d="M1 2l6 5 6-5" stroke="#fff" fill="none"/></svg>MESAGE BOARD</span><span class="sep">/</span>
  <span><svg viewBox="0 0 14 13"><circle cx="8" cy="4" r="3" fill="#444"/><rect x="6.5" y="5" width="2" height="8" fill="#444" transform="rotate(20 7 9)"/></svg>LOGIN</span><span class="sep">/</span>
  <span><svg viewBox="0 0 14 13"><circle cx="6" cy="5.5" r="4" stroke="#444" stroke-width="1.6" fill="none"/><path d="M9 8.5l4 4" stroke="#444" stroke-width="1.8"/></svg>SEARCH</span>
</nav>

<nav class="abs main-nav">
  <a style="left:124px">HOME</a><a style="left:187px">ABOUT US</a><a style="left:269px">MEBERSHIP</a>
  <a style="left:357px">BUYERS</a><a style="left:424px">SUPPLIERS</a><a style="left:510px">GOVERNMENT DATA</a>
  <a style="left:643px">ADVERTISE</a><a style="left:727px">MEDIA</a><a style="left:792px">CONTACT US</a>
</nav>

<section class="abs hero" role="img" aria-label="Photo of a white passenger jet flying above the clouds in a blue sky">
  <div class="abs hero-caption"></div>
  <div class="abs hero-title">GOVERNMENT BIDDING? DETAILED LOGISTICS &amp; NOTIFICATION</div>
  <div class="abs hero-text">Updated sollicitation information. Receive E-mail notification when a Government sollicita-tion&nbsp; matches your inventory!</div>
  <div class="abs hero-btn">READ MORE</div>
  <div class="abs dots"><i class="on"></i><i></i><i></i><i></i></div>
</section>

<article class="abs card" style="left:114px">
  <div class="card-media" role="img" aria-label="Hand holding a lightbulb made of gears on a chalkboard" style="background:radial-gradient(circle at 50% 50%,#8a8a8a,#3a3a3a)"></div>
  <h3>SOLUTIONS</h3>
  <p>Sed ut perspiciatis unde omnis iste natus error sit voluptatem</p>
  <div class="more">Learn More &nbsp;›</div>
</article>
<article class="abs card" style="left:308px">
  <div class="card-media" role="img" aria-label="Silhouettes of people holding hands at sunset" style="background:linear-gradient(#7a5a40,#e28b2e 60%,#3a2414)"></div>
  <h3>OUR COMMUNITY</h3>
  <p>Sed ut perspiciatis unde omnis iste natus error sit voluptatem</p>
  <div class="more">Learn More ›</div>
</article>
<article class="abs card" style="left:500px">
  <div class="card-media" role="img" aria-label="Engineers in hard hats in front of industrial silos" style="background:linear-gradient(#a9bfdc,#c8ccd2 50%,#6a7d9a)"></div>
  <h3>INDUSTRY CONNECTION</h3>
  <p>Sed ut perspiciatis unde omnis iste natus error sit voluptatem</p>
  <div class="more">Learn More &nbsp;›</div>
</article>
<article class="abs card" style="left:697px">
  <div class="card-media" role="img" aria-label="Business team giving thumbs up" style="background:linear-gradient(90deg,#2b2b2b,#8a7a70 50%,#d8cfc8)"></div>
  <h3>MEMBER ADVANTAGES</h3>
  <p>Sed ut perspiciatis unde omnis iste natus error sit voluptatem</p>
  <div class="more">Learn More ›</div>
</article>

<section class="welcome">
  <h2 class="abs section-title" style="left:117px;top:740px">WELCOME</h2>
  <div class="abs rule" style="left:117px;top:766px;width:353px"></div>
  <p style="top:775px">Sed ut perspiciatis unde omnis iste natus error sit voluptatem accusantium doloremque laudantium, totam rem aperiam, eaque ipsa quae ab illo inventore veritatis et quasi architecto beatae vitae dicta sunt explicabo.</p>
  <p style="top:830px">Nemo enim ipsam voluptatem quia voluptas sit aspernatur aut odit aut fugit, sed quia consequuntur magni dolores eos qui ratione voluptatem sequi nesciunt. Neque porro quisquam est, qui dolorem ipsum quia dolor sit amet, consectetur, adipisci velit, sed quia non numquam eius modi tempora incidunt ut labore et dolore magnam aliquam quaerat voluptatem.</p>
  <p style="top:913px">&nbsp;Ut enim ad minima veniam, quis nostrum exercitationem ullam corporis suscipit laborio-sam, nisi ut aliquid ex ea commodi consequatur? Quis autem vel eum iure reprehenderit qui in ea voluptate velit esse quam nihil molestiae consequatur, vel illum qui dolorem eum fugiat quo voluptas nulla pariatur</p>
</section>

<section class="events">
  <h2 class="abs section-title" style="left:513px;top:737px">UPCOMING NEWS &amp; EVENTS</h2>
  <svg class="abs" style="left:845px;top:740px" width="22" height="16" viewBox="0 0 22 16"><path d="M8 2L2 8l6 6M14 2l6 6-6 6" stroke="#222" stroke-width="2.4" fill="none"/></svg>
  <div class="abs rule" style="left:513px;top:766px;width:353px"></div>

  <div class="abs news-thumb" style="top:780px;background:linear-gradient(#6f8cb0,#2e3f5a)" role="img" aria-label="Military helicopter"></div>
  <div class="abs news-text" style="top:780px">Sed ut perspiciatis unde omnis iste natus error sit voluptatem accusan-tium doloremque laudantium, totam rem aperiam, eaque ipsa quae ab illo</div>
  <div class="abs news-date" style="top:818px">July 28 2014</div>
  <div class="abs rule" style="left:513px;top:838px;width:353px"></div>

  <div class="abs news-thumb" style="top:850px;background:linear-gradient(#4f7d6a,#9fb8ae)" role="img" aria-label="Jets flying in formation"></div>
  <div class="abs news-text" style="top:850px">Sed ut perspiciatis unde omnis iste natus error sit voluptatem accusan-tium doloremque laudantium, totam rem aperiam, eaque ipsa quae ab illo</div>
  <div class="abs news-date" style="top:888px">July 28 2014</div>
  <div class="abs rule" style="left:513px;top:908px;width:353px"></div>

  <div class="abs news-thumb" style="top:920px;background:linear-gradient(#8a9ec0,#b06a4a)" role="img" aria-label="Airliner on a runway at dusk"></div>
  <div class="abs news-text" style="top:920px">Sed ut perspiciatis unde omnis iste natus error sit voluptatem accusan-tium doloremque laudantium, totam rem aperiam, eaque ipsa quae ab</div>
  <div class="abs news-date" style="top:958px">July 28 2014</div>
  <div class="abs rule" style="left:513px;top:978px;width:353px"></div>
</section>

<footer>
  <div class="abs footer"></div>
  <div class="abs f-col" style="left:120px"><span>Home</span><span>About</span><span>News</span><span>Services</span><span>What We Do</span><span>Contact Us</span></div>
  <div class="abs f-col" style="left:234px"><span>Grief &amp; Healing</span><span>Resources</span><span>Plan Now</span><span>Locations</span><span>Privacy Policy</span><span>Terms &amp; Conditions</span></div>
  <div class="abs f-col" style="left:381px"><span>Healing</span><span>Resources</span><span>Plan Now</span><span>Locations</span><span>Privacy Policy</span><span>Terms &amp; Conditions</span></div>
  <div class="abs news-head">NEWSLETTER SIGN UP</div>
  <div class="abs field" style="top:1050px">Enter Name</div>
  <div class="abs field" style="top:1085px">Enter Email Address</div>
  <div class="abs signup">SIGN UP</div>
  <div class="abs contact">Shooting Sports Sed ut perspiciatis unde,sit voluptatem a<br><br>Phone: (000) 000 0000<br>Fax: (000) 000 0000</div>
  <div class="abs social" aria-label="Social links"><i></i><i></i><i></i><i></i><i></i></div>
  <div class="abs footer-base">© 2014 GearHive. All Rights Reserved.</div>
</footer>

</body>
</html>
```